Valmora Health a direct primary care practice needs a beautiful and customer friendly website

We need a website to showcase our new medical practice. We want to enhance the customer experience and make it easy to navigate to the desired page by placing pillar pages on the home screen. the website needs to be clean and bright.

Target Market(s)

Uninsured, Small businesses that can't afford to offer employees insurance.

Industry/Entity Type

Healthcare

Coding

Coded - Design and coding required

Font styles to use
Serif
Sans Serif

Colors
0592cd
3377b5
0355a3
9bcb3c
acd136

Requirements
Must have
• Must be user friendly, must have pillar pages to help boost SEO ranking, clean and bright, must be close to the in colors to the attached logo.

Content will be very similar to www.quillbrookhealth.example
Nice to have
• Clean and easy to read font

```html
<!DOCTYPE html>
<html lang="en">
<head>
<meta charset="utf-8">
<title>Valmora Health – Direct Primary Care</title>
<link rel="stylesheet" href="https://fonts.googleapis.com/css2?family=Arimo:wght@400;700&family=Lato:wght@400;700&display=swap">
<style>
:root{
  --blue:#0a45a6;
  --green:#8cc43c;
  --ink:#111;
  --body:#333;
  --footer:#0b0b0d;
  --accent:#1b6fcf;
  --white:#fff;
}
*{box-sizing:border-box;margin:0;padding:0}
html,body{width:1200px;height:3546px;overflow:hidden}
body{position:relative;font-family:"Lato",sans-serif;color:var(--body);background:var(--white)}
.abs{position:absolute}
h1,h2,h3{font-family:"Arimo",sans-serif;font-weight:700}

/* header */
.site-header{position:absolute;left:0;top:0;width:1200px;height:101px;background:var(--blue)}
.brand{position:absolute;left:113px;top:34px;color:#fff;font-family:"Lato",sans-serif;font-size:31px;letter-spacing:2px;text-transform:uppercase;display:flex;align-items:center;gap:10px;white-space:nowrap}
.brand-dot{width:11px;height:11px;border-radius:50%;background:#fff}
.top-contact{position:absolute;top:13px;display:flex;align-items:center;gap:10px;color:#fff;font-size:16px;font-weight:700;white-space:nowrap}
.icon-ring{width:40px;height:40px;border:2px solid #fff;border-radius:50%;display:flex;align-items:center;justify-content:center}
.join{position:absolute;left:963px;top:12px;width:125px;height:42px;border:2px solid #fff;border-radius:22px;color:#fff;font:700 17px "Arimo",sans-serif;display:flex;align-items:center;justify-content:center}
.main-nav{position:absolute;top:71px;left:0;width:1200px;height:20px}
.main-nav a{position:absolute;color:#fff;font:700 16px "Lato",sans-serif;text-decoration:none}
.main-nav a.active::after{content:"";position:absolute;left:0;right:0;top:26px;height:2px;background:#fff}

/* hero */
.hero{position:absolute;left:0;top:101px;width:1200px;height:616px;background:linear-gradient(100deg,#6a5a4e 0%,#b9a99a 30%,#d8d2c9 55%,#c9b7a4 75%,#8e7a68 100%)}
.hero h1{position:absolute;left:0;width:1200px;top:88px;text-align:center;color:#fff;font-size:53px;line-height:54px}
.btn-green{position:absolute;left:506px;top:210px;width:188px;height:57px;border-radius:29px;background:var(--green);color:#fff;font:700 18px "Arimo",sans-serif;display:flex;align-items:center;justify-content:center}
.dots{position:absolute;top:566px;left:558px;display:flex;gap:10px}
.dots span{width:12px;height:12px;border-radius:50%;background:rgba(255,255,255,.5)}
.dots span:first-child{background:#fff}

/* step up */
.video{position:absolute;left:113px;top:802px;width:469px;height:366px;background:linear-gradient(135deg,#e8e4de,#c7bfb2 60%,#9e8f7c)}
.play{position:absolute;left:205px;top:162px;width:58px;height:42px;background:#e52620;border-radius:11px}
.play::after{content:"";position:absolute;left:22px;top:12px;border-left:16px solid #fff;border-top:9px solid transparent;border-bottom:9px solid transparent}
.copy{position:absolute;left:641px;width:447px}
.copy h2{color:var(--ink);font-size:38px;margin-bottom:14px}
.copy p{font-size:13px;line-height:25.8px;text-align:justify;color:#333}
.copy h4{font:700 13.5px "Arimo",sans-serif;color:#111;margin:6px 0 5px}

/* bands */
.band{position:absolute;left:0;width:1200px;background:linear-gradient(180deg,#1b5ab3,#0e4aa5)}
.band h2{position:absolute;left:0;width:1200px;text-align:center;color:#fff;font-size:35px}
.band-intro{position:absolute;left:156px;width:888px;top:143px;text-align:center;color:#fff;font-size:15px;line-height:26.7px}
.card{position:absolute;top:328px;width:294px;height:323px;border:2px solid #fff;color:#fff;text-align:center}
.card svg{margin:26px auto 0;display:block}
.card h3{font:700 19px "Lato",sans-serif;margin:14px 0 10px}
.card p{font-size:15.5px;line-height:26.7px;padding:0 22px}
.btn-outline{display:inline-flex;align-items:center;justify-content:center;width:143px;height:42px;border:1.5px solid #fff;color:#fff;font:700 14px "Arimo",sans-serif;margin-top:20px}

/* fewer patients */
.photo-frame{position:absolute;left:104px;top:2075px;width:470px;height:370px;background:var(--green)}
.photo{position:absolute;left:113px;top:2083px;width:469px;height:366px;background:linear-gradient(120deg,#9aa9b8,#e8ecef 50%,#cfd6dd)}

/* appointment */
.field{position:absolute;height:51px;border:1.5px solid rgba(255,255,255,.85);color:#fff;font-size:15px;padding:0 12px;display:flex;align-items:center}
.field.msg{align-items:flex-start;padding-top:16px}
.btn-submit{position:absolute;left:476px;top:455px;width:246px;height:52px;border:1.5px solid #fff;color:#fff;font:700 15px "Arimo",sans-serif;display:flex;align-items:center;justify-content:center}

/* footer */
.site-footer{position:absolute;left:0;top:3108px;width:1200px;height:438px;background:var(--footer);color:#fff}
.foot-brand{position:absolute;left:112px;top:82px;font-size:20px;letter-spacing:1px;text-transform:uppercase;white-space:nowrap}
.site-footer h5{position:absolute;font:700 19px "Lato",sans-serif;text-transform:uppercase;letter-spacing:-.3px;white-space:nowrap}
.site-footer h5::after{content:"";position:absolute;left:0;top:34px;width:36px;height:2px;background:var(--accent)}
.site-footer h5.plain::after{display:none}
.social{position:absolute;left:111px;top:3330px;display:flex;gap:6px}
.social span{width:49px;height:49px;border-radius:50%;background:var(--accent)}
.quick{position:absolute;left:354px;top:115px;list-style:none;font-size:15px;line-height:26.7px}
.contact-row{position:absolute;left:556px;display:flex;align-items:center;gap:12px;font-size:15px;line-height:22px}
.c-icon{width:33px;height:33px;border-radius:50%;background:var(--accent);display:flex;align-items:center;justify-content:center;flex:none}
.map{position:absolute;left:880px;top:118px;width:210px;height:211px;background:linear-gradient(135deg,#f3f3f1,#e6e4df)}
.copyright{position:absolute;left:0;width:1200px;top:390px;text-align:center;font-size:15px}
</style>
</head>
<body>

<header class="site-header">
  <div class="brand"><span class="brand-dot"></span>Valmora Health</div>
  <div class="top-contact" style="left:516px">
    <span class="icon-ring"><svg width="18" height="18" viewBox="0 0 24 24"><path fill="#fff" d="M6.6 10.8a15 15 0 0 0 6.6 6.6l2.2-2.2a1 1 0 0 1 1-.25 11.4 11.4 0 0 0 3.6.57 1 1 0 0 1 1 1V20a1 1 0 0 1-1 1A17 17 0 0 1 3 4a1 1 0 0 1 1-1h3.5a1 1 0 0 1 1 1c0 1.25.2 2.45.57 3.57a1 1 0 0 1-.25 1z"/></svg></span>555 - 014 - 2270
  </div>
  <div class="top-contact" style="left:712px">
    <span class="icon-ring"><svg width="18" height="14" viewBox="0 0 18 14"><rect x="1" y="1" width="16" height="12" fill="none" stroke="#fff" stroke-width="2"/><path d="M1 1l8 7 8-7" fill="none" stroke="#fff" stroke-width="2"/></svg></span>hello@valmora.example
  </div>
  <div class="join">JOIN US</div>
  <nav class="main-nav">
    <a class="active" href="#" style="left:456px">Home</a>
    <a href="#" style="left:528px">About</a>
    <a href="#" style="left:597px">Services</a>
    <a href="#" style="left:712px">Employers</a>
    <a href="#" style="left:814px">Pricing</a>
    <a href="#" style="left:893px">FAQ</a>
    <a href="#" style="left:952px">Blog</a>
    <a href="#" style="left:1013px">Contact Us</a>
  </nav>
</header>

<section class="hero" role="img" aria-label="Smiling doctor giving a high five to a young patient">
  <h1>EXPECT MORE FROM<br>YOUR DOCTOR</h1>
  <div class="btn-green">GET STARTED</div>
  <svg class="abs" style="left:68px;top:287px" width="22" height="40" viewBox="0 0 22 40"><path d="M20 2L2 20l18 18" fill="none" stroke="#fff" stroke-width="2"/></svg>
  <svg class="abs" style="left:1108px;top:287px" width="22" height="40" viewBox="0 0 22 40"><path d="M2 2l18 18L2 38" fill="none" stroke="#fff" stroke-width="2"/></svg>
  <div class="dots"><span></span><span></span><span></span><span></span></div>
</section>

<div class="video" role="img" aria-label="Video still of a mother and son talking with a doctor"><span class="play"></span></div>
<article class="copy" style="top:806px">
  <h2>TAKE A STEP UP</h2>
  <p>Our direct primary clinic in Huntington Beach isn’t paid by insurance companies for codes and data. We are paid by you. That’s why we have the same goals you do: to keep you healthy, use as few medications as possible, avoid unnecessary care and save you time and money.</p>
  <h4>ENJOY MORE PERSONAL MEDICAL CARE IN HUNTINGTON BEACH</h4>
  <p>We are dedicated to restoring your belief in medical care by giving you a more personal and affordable experience with your family doctor. Forget about your past experiences with feeling over-charged and underappreciated. Direct primary care clinics are designed to give you the medical care you deserve without all the bureaucracy. We are here for you, and you’ll notice the difference.</p>
</article>

<section class="band" style="top:1249px;height:746px">
  <h2 style="top:88px">BENEFITS OF OUR PRIMARY CARE CLINIC</h2>
  <p class="band-intro">We offer unlimited office visits with no copay and as much time as you need. We are designed to accommodate a much smaller group of patients so that your appointments are not being rushed and our family doctors can take all the time they need. We provide the added convenience of an onsite wholesale pharmacy, X-ray, drug testing lab, and ultrasound so that you don’t need to travel or wait for these specialty services. Our primary care clinic in Huntington Beach, California prides itself on a far more personal experience when it comes to communication. We are always available for our patients via phone, email, and text. Finally, all of our services are included in your membership, or offered at-cost, so that you’re never paying extra for the services you need.</p>
  <div class="card" style="left:145px">
    <svg width="64" height="64" viewBox="0 0 64 64"><circle cx="32" cy="32" r="30" fill="none" stroke="#fff" stroke-width="2.5"/><path d="M27 18h10v9h9v10h-9v9H27v-9h-9V27h9z" fill="none" stroke="#fff" stroke-width="2.5"/></svg>
    <h3>BENEFITS</h3>
    <p>We offer unlimited office visits and personal communications via phone, secure e-mail and text.</p>
    <span class="btn-outline">LEARN MORE</span>
  </div>
  <div class="card" style="left:453px">
    <svg width="64" height="64" viewBox="0 0 64 64"><circle cx="32" cy="32" r="30" fill="none" stroke="#fff" stroke-width="2.5"/><path d="M24 25a8 8 0 1 1 12 7c-3 2-4 3-4 7" fill="none" stroke="#fff" stroke-width="3.5"/><circle cx="32" cy="46" r="2.5" fill="#fff"/></svg>
    <h3>QUESTIONS?</h3>
    <p>How does this work? What about insurance? Do you work with Medicare? Here are some</p>
    <span class="btn-outline">LEARN MORE</span>
  </div>
  <div class="card" style="left:761px">
    <svg width="64" height="64" viewBox="0 0 64 64"><circle cx="32" cy="32" r="30" fill="none" stroke="#fff" stroke-width="2.5"/><path d="M32 14v18l10 10" fill="none" stroke="#fff" stroke-width="3"/></svg>
    <h3>OFFICE HOURS</h3>
    <p>MWF 9:00 AM – 5:00 PM<br>T/Th 8:00 AM - 4:00 PM<br>Call or text us today at<br>555 - 014 - 2270<br>For our members, we are always on call.</p>
  </div>
</section>

<div class="photo-frame"></div>
<div class="photo" role="img" aria-label="Doctor with clipboard consulting a smiling male patient"></div>
<article class="copy" style="top:2094px">
  <h2 style="font-size:32px;margin-bottom:18px">FEWER PATIENTS</h2>
  <p>Did you know that most primary care physicians have between 2,500-3,500 patients? Quillbrook Health physicians will limit their practice to no more than 800 patients. This means that your family medicine doctor can spend more time with you when you need it. It also means that when they are not actively seeing a patient, they are able to coordinate your care and research using the latest advances in treatments. Your well-being is our priority, and the reason for why we do what we do. You will notice the difference by finally having a Huntington Beach family medicine doctor that has the time to really care about you and your healthcare above all else.</p>
</article>

<section class="band" style="top:2533px;height:575px;background:linear-gradient(180deg,#1a57b0,#1452ad)">
  <h2 style="top:100px;font-size:40px">MAKE AN APPOINTMENT</h2>
  <div class="field" style="left:206px;top:177px;width:385px">First Name</div>
  <div class="field" style="left:607px;top:177px;width:385px">Last Name</div>
  <div class="field" style="left:206px;top:244px;width:385px">Email</div>
  <div class="field" style="left:607px;top:244px;width:385px">Phone</div>
  <div class="field msg" style="left:206px;top:312px;width:788px;height:105px">How Can We Help?</div>
  <div class="btn-submit">MAKE AN APPOINTMENT</div>
</section>

<footer class="site-footer">
  <div class="foot-brand">Valmora Health</div>
  <h5 class="plain" style="left:110px;top:180px">Follow Us On</h5>
  <h5 style="left:354px;top:76px">Quick Links</h5>
  <ul class="quick"><li>Home</li><li>About</li><li>Services</li><li>Employers</li><li>Pricing</li><li>FAQ</li><li>Blog</li><li>Contact Us</li></ul>
  <h5 style="left:554px;top:76px">Contact Details</h5>
  <div class="contact-row" style="top:124px"><span class="c-icon"><svg width="14" height="18" viewBox="0 0 14 18"><path d="M7 0a7 7 0 0 1 7 7c0 5-7 11-7 11S0 12 0 7a7 7 0 0 1 7-7z" fill="#fff"/><circle cx="7" cy="7" r="2.5" fill="#1b6fcf"/></svg></span><span>123 Avenue name, City name<br>10150, United States</span></div>
  <div class="contact-row" style="top:195px;font-weight:700"><span class="c-icon"><svg width="15" height="15" viewBox="0 0 24 24"><path fill="#fff" d="M6.6 10.8a15 15 0 0 0 6.6 6.6l2.2-2.2a1 1 0 0 1 1-.25 11.4 11.4 0 0 0 3.6.57 1 1 0 0 1 1 1V20a1 1 0 0 1-1 1A17 17 0 0 1 3 4a1 1 0 0 1 1-1h3.5a1 1 0 0 1 1 1c0 1.25.2 2.45.57 3.57a1 1 0 0 1-.25 1z"/></svg></span>555 014 2270</div>
  <div class="contact-row" style="top:249px"><span class="c-icon"><svg width="15" height="11" viewBox="0 0 18 14"><rect x="1" y="1" width="16" height="12" fill="none" stroke="#fff" stroke-width="2"/><path d="M1 1l8 7 8-7" fill="none" stroke="#fff" stroke-width="2"/></svg></span>hello@valmora.example</div>
  <div class="contact-row" style="top:301px"><span class="c-icon"><svg width="16" height="16" viewBox="0 0 16 16"><circle cx="8" cy="8" r="7" fill="none" stroke="#fff" stroke-width="2"/><path d="M8 4v4l3 2" fill="none" stroke="#fff" stroke-width="2"/></svg></span>Monday to Friday 8am – 5pm</div>
  <h5 style="left:880px;top:76px">Location Map</h5>
  <div class="map" role="img" aria-label="Street map showing the clinic location"></div>
  <p class="copyright">© 2021 Valmora Health. All Rights Reserved</p>
</footer>
<div class="social" aria-label="Social media links"><span></span><span></span><span></span></div>

</body>
</html>
```